White Paper and One-Page Advertisement for TELVORISH-QM

I need both documents to be better formatted and designed so they look professional, not something someone with mediocre word skills put together. They will go out to 1000s of industry professionals, and they need to look sharp. I need them to have my company's color palate logo, and branding on it similar to how it is now, but better. Please do not change any of the written content, but it can be arranged in any other format you think is better. Smart art and things i've already used can be omitted in favor of better designs. The developer is free to use their creativity. White paper should not be longer than the three pages unless necessary.

Target Market(s)

Life Sciences supply chain professionals

Colors
33b8a4
0592cd
9bcb3c
fbee3e
3277b5

Requirements
Must have
• Must be professional looking and not look like something done in word. Please use the color palate as seen on the documents.
Should not have
• Any changes to the written content.

```html
<!DOCTYPE html>
<html lang="en">
<head>
<meta charset="utf-8">
<title>White Paper Cover Pages – TELVORISH-QM</title>
<link rel="stylesheet" href="https://fonts.googleapis.com/css2?family=Montserrat:wght@400;500;600;700;800&family=Raleway:wght@400;500&display=swap">
<style>
  :root{
    --board:#555555;
    --paper:#ffffff;
    --green:#8cc43f;
    --green-deep:#76b22e;
    --green-soft:#a9d468;
    --charcoal:#4a4a4a;
    --ink:#222222;
    --brand:#1f8a68;
    --label:#9bcb3c;
    --caption:#f2f2f2;
    --photo-light:#e9ddd2;
    --photo-mid:#c9b7a6;
    --photo-dark:#9a8a7c;
    --portrait-light:#d7dfe8;
    --portrait-mid:#9db3cf;
  }
  *{margin:0;padding:0;box-sizing:border-box}
  html,body{width:1200px;height:887px;overflow:hidden;background:var(--board)}
  .board{position:relative;width:1200px;height:887px;background:var(--board);font-family:"Montserrat",sans-serif}

  .cover{position:absolute;top:59px;width:487px;height:686px;background:var(--paper);overflow:hidden;box-shadow:0 14px 18px -10px rgba(0,0,0,.45)}
  .cover--one{left:79px}
  .cover--two{left:624px}
  .cover__art{position:absolute;inset:0;width:100%;height:100%}

  .brand{position:absolute;display:flex;align-items:center;gap:7px}
  .brand__dot{width:22px;height:22px;border-radius:50%;border:3px solid var(--green)}
  .brand__name{font-family:"Montserrat",sans-serif;font-weight:800;font-size:19px;letter-spacing:.5px;color:var(--brand)}
  .cover--one .brand{left:22px;top:74px}
  .cover--two .brand{right:22px;top:92px}

  .title{font-family:"Montserrat",sans-serif;font-weight:800;line-height:1;letter-spacing:-.2px}
  .title__accent{color:var(--green)}
  .title__main{color:var(--charcoal)}
  .subtitle{font-family:"Raleway",sans-serif;font-weight:500;color:var(--ink)}
  .byline{font-family:"Montserrat",sans-serif;font-weight:600;color:var(--green);font-size:11px}
  .byline__sep{margin:0 7px}

  .cover--one .heading{position:absolute;right:23px;top:21px;text-align:right}
  .cover--one .title{font-size:30px}
  .cover--one .title span{display:block;height:30px}
  .cover--one .subtitle{font-size:10.4px;line-height:13.5px;margin-top:8px}
  .cover--one .byline{margin-top:7px}

  .site{position:absolute;left:0;right:0;top:651px;display:flex;align-items:center;justify-content:center;gap:10px;color:var(--paper);font-family:"Raleway",sans-serif;font-size:10px;letter-spacing:2.4px}
  .site__rule{width:52px;height:1px;background:var(--paper)}

  .cover--two .heading{position:absolute;left:0;right:0;top:532px;text-align:center}
  .cover--two .title{font-size:31.5px}
  .cover--two .title span{display:block;height:33px}
  .cover--two .subtitle{font-size:10.4px;line-height:13.5px;margin-top:8px}
  .cover--two .footer{position:absolute;left:29px;right:31px;top:659px;display:flex;justify-content:space-between;align-items:center}
  .cover--two .footer .site-link{font-family:"Raleway",sans-serif;font-size:10px;color:var(--ink)}

  .sample-label{position:absolute;top:762px;font-family:"Raleway",sans-serif;font-size:19px;color:var(--label);letter-spacing:.2px}
  .sample-label--one{left:75px}
  .sample-label--two{left:624px}
  .board-caption{position:absolute;left:0;right:0;top:827px;text-align:center;font-family:"Raleway",sans-serif;font-size:18px;color:var(--caption)}
</style>
</head>
<body>
<main class="board">

  <article class="cover cover--one">
    <svg class="cover__art" viewBox="0 0 608 857" preserveAspectRatio="none">
      <defs>
        <radialGradient id="infantTone" cx="50%" cy="45%" r="60%">
          <stop offset="0" stop-color="var(--photo-light)"/>
          <stop offset=".65" stop-color="var(--photo-mid)"/>
          <stop offset="1" stop-color="var(--photo-dark)"/>
        </radialGradient>
      </defs>
      <polygon points="0,121 400,330 400,857 0,857" fill="var(--green)"/>
      <polygon points="608,281 608,857 420,700 470,520" fill="var(--charcoal)"/>
      <polygon points="400,690 608,857 0,857 0,760" fill="var(--green)"/>
      <circle cx="224" cy="526" r="290" fill="var(--green-deep)" opacity=".35"/>
      <circle cx="224" cy="526" r="270" fill="var(--green-soft)" opacity=".35"/>
      <circle cx="224" cy="526" r="255" fill="var(--paper)"/>
      <path d="M36,369 A245,245 0 0 1 452,606" fill="none" stroke="var(--green)" stroke-width="14"/>
      <polygon points="440,650 478,612 428,597" fill="var(--green)"/>
      <circle role="img" aria-label="Photo of a baby in a knitted hooded sweater" cx="224" cy="526" r="222" fill="url(#infantTone)"/>
    </svg>

    <div class="brand"><span class="brand__dot"></span><span class="brand__name">TELVORISHQM</span></div>

    <header class="heading">
      <h1 class="title">
        <span class="title__accent">CHANGING</span>
        <span class="title__accent">PHARMA’S</span>
        <span class="title__main">PARADIGM OF</span>
        <span class="title__main">WASTE</span>
      </h1>
      <p class="subtitle">How Pharma’s Demand Volatility Could<br>Be Costing You Millions in Material<br>Write-downs &amp; Procurement</p>
      <p class="byline">DANA WHITLOW<span class="byline__sep">|</span>AUGUST 2018</p>
    </header>

    <div class="site"><span class="site__rule"></span>WWW.TELVORISHQM.COM<span class="site__rule"></span></div>
  </article>

  <article class="cover cover--two">
    <svg class="cover__art" viewBox="0 0 608 857" preserveAspectRatio="none">
      <defs>
        <radialGradient id="infantToneTwo" cx="50%" cy="40%" r="60%">
          <stop offset="0" stop-color="var(--photo-light)"/>
          <stop offset=".65" stop-color="var(--photo-mid)"/>
          <stop offset="1" stop-color="var(--photo-dark)"/>
        </radialGradient>
        <radialGradient id="elderTone" cx="50%" cy="40%" r="60%">
          <stop offset="0" stop-color="var(--portrait-light)"/>
          <stop offset="1" stop-color="var(--portrait-mid)"/>
        </radialGradient>
      </defs>
      <path d="M-62,333 A268,268 0 0 1 310,109" fill="none" stroke="var(--charcoal)" stroke-width="16"/>
      <path d="M454,423 A258,258 0 0 0 378,164" fill="none" stroke="var(--green)" stroke-width="14"/>
      <polygon points="345,134 398,148 362,186" fill="var(--green)"/>
      <path d="M-44,423 A258,258 0 0 0 340,585" fill="none" stroke="var(--green)" stroke-width="14"/>
      <polygon points="372,628 322,612 356,578" fill="var(--green)"/>
      <circle role="img" aria-label="Photo of a baby in a knitted hooded sweater" cx="205" cy="356" r="245" fill="url(#infantToneTwo)"/>
      <path d="M507,394 A130,130 0 0 1 377,619" fill="none" stroke="var(--charcoal)" stroke-width="14"/>
      <circle cx="442" cy="506" r="122" fill="var(--paper)"/>
      <circle role="img" aria-label="Photo of a smiling elderly woman in a light blue shirt" cx="442" cy="506" r="114" fill="url(#elderTone)"/>
    </svg>

    <div class="brand"><span class="brand__dot"></span><span class="brand__name">TELVORISHQM</span></div>

    <header class="heading">
      <h1 class="title">
        <span class="title__accent">CHANGING PHARMA’S</span>
        <span class="title__main">PARADIGM OF WASTE</span>
      </h1>
      <p class="subtitle">How Pharma’s Demand Volatility Could Be Costing You Millions in Material<br>Write-downs &amp; Procurement</p>
    </header>

    <div class="footer">
      <p class="byline">DANA WHITLOW<span class="byline__sep">&nbsp;&nbsp;|&nbsp;&nbsp;</span>AUGUST 2018</p>
      <p class="site-link">WWW.TELVORISHQM.COM</p>
    </div>
  </article>

  <p class="sample-label sample-label--one">COVER PAGE SAMPLE 1</p>
  <p class="sample-label sample-label--two">COVER PAGE SAMPLE 2</p>
  <p class="board-caption">White Paper Advertisement Cover Page for TELVORISH-QM</p>

</main>
</body>
</html>
```